Flyer Design for Private Car Service

Flyer should cater to Business Travelers and Executives who travel Business Class or First Class.
Flyer should include images attached.
Flyer should include the below text
Dallas to Austin
Quorvan Ride
• Travel Dallas to Austin in a new 2025 Norvak Tressel for $499 one-way
• Trip includes a Uniformed Chauffeur who has a Commercial Drivers License (CDL)
• You can Schedule Chauffeur Pickup at Your Home in Dallas
• Our Chauffeur will Drop You Off at Your Final Destination in Austin
• You can Schedule Chauffeur Return Pickup in Austin and Return Back to Dallas.
• We offer Faster Times on Door-to-Door Travel than Bluequill Airways
• We offer Comparable Prices on Door-to-Door Travel Times than Bluequill Airways
• All of our trips are insured with $500k of commercial auto insurance
• Our Passengers can Talk on Cell Phone & Conduct Kavlo calls Throughout Travel
• Our Passengers have Maximum Privacy, Comfort and First-Class Amenities.
• Our Passengers Avoid Marrow Pike Airfield and QHN Airport hassles & delays
• Member Tellbrook Chamber of Commerce, Pindle Chamber of Commerce.
• Book your trip today at www.quorvanride.example
Target Market(s)
Business Travelers
Look and feel

```html
<!DOCTYPE html>
<html lang="en">
<head>
<meta charset="utf-8">
<title>Dallas to Austin – Quorvan Ride</title>
<link rel="stylesheet" href="https://fonts.googleapis.com/css2?family=Montserrat:wght@400;500;700;800&display=swap">
<style>
  :root {
    --red: #ec1c24;
    --black: #0d0d0d;
    --ink: #1a1a1a;
    --cream: #e8e4de;
    --blush: #e9d4c5;
    --white: #ffffff;
  }
  * { margin: 0; padding: 0; box-sizing: border-box; }
  html, body { width: 928px; height: 1200px; overflow: hidden; }
  body { background: var(--cream); font-family: "Montserrat", sans-serif; }
  .flyer {
    position: relative;
    width: 928px;
    height: 1200px;
    overflow: hidden;
    background: linear-gradient(180deg, var(--cream) 0%, var(--cream) 45%, var(--blush) 100%);
  }
  .fleet-photo {
    position: absolute;
    left: 0; top: 498px;
    width: 928px; height: 290px;
    background: linear-gradient(180deg, #d9d4cf 0%, #c9c6c3 35%, #6f6d6e 60%, #b9b2ad 78%, rgba(233,212,197,0) 100%);
  }
  .brand {
    position: absolute;
    left: 0; top: 140px;
    width: 576px;
    text-align: center;
    font-family: "Montserrat", sans-serif;
    font-weight: 500;
    font-size: 44px;
    letter-spacing: 3px;
    line-height: 1;
    color: var(--black);
  }
  .route {
    position: absolute;
    left: 36px; width: 500px;
    color: var(--red);
    font-weight: 800;
    font-size: 121px;
    line-height: 1;
    letter-spacing: -2px;
    text-align: center;
  }
  .route-from { top: 243px; }
  .route-to { top: 400px; }
  .route-divider {
    position: absolute;
    left: 48px; top: 373px;
    width: 476px; height: 1.5px;
    background: var(--red);
  }
  .route-joiner {
    position: absolute;
    left: 258px; top: 348px;
    width: 52px; height: 52px;
    border-radius: 50%;
    background: var(--cream);
    box-shadow: 0 3px 6px rgba(0,0,0,0.25);
    color: var(--red);
    font-weight: 800;
    font-size: 22px;
    display: flex; align-items: center; justify-content: center;
  }
  .photo-arrival {
    position: absolute;
    left: 538px; top: -55px;
    width: 440px; height: 440px;
    border-radius: 50%;
    background: linear-gradient(135deg, #8d8d8f 0%, #3b3c40 45%, #1c1c20 100%);
    border: 3px solid var(--black);
  }
  .photo-chauffeurs {
    position: absolute;
    left: 662px; top: 266px;
    width: 304px; height: 304px;
    border-radius: 50%;
    background: linear-gradient(160deg, #b8cbd6 0%, #7d8890 35%, #2a2a2c 70%, #1c1c1c 100%);
    border: 5px solid var(--red);
  }
  .price-badge {
    position: absolute;
    left: 555px; top: 226px;
    width: 170px; height: 170px;
    border-radius: 50%;
    background: var(--red);
    box-shadow: 8px 8px 0 rgba(120,120,120,0.55);
    text-align: center;
    color: var(--black);
  }
  .price-amount {
    margin-top: 36px;
    font-weight: 800;
    font-size: 62px;
    line-height: 1;
    letter-spacing: -1px;
  }
  .price-amount sup { font-size: 28px; vertical-align: 26px; margin-right: 2px; }
  .price-term {
    color: var(--white);
    font-weight: 500;
    font-size: 27px;
    line-height: 1;
    margin-top: 2px;
  }
  .features {
    position: absolute;
    left: 55px; top: 790px;
    width: 850px;
    display: grid;
    grid-template-columns: 408px 442px;
    row-gap: 12px;
    list-style: none;
  }
  .feature {
    display: flex; align-items: center;
    height: 36px;
    font-size: 14.6px;
    font-weight: 500;
    line-height: 17.6px;
    color: var(--ink);
    white-space: nowrap;
  }
  .feature-mark {
    flex: none;
    width: 50px; height: 30px;
    margin-right: 26px;
    border-radius: 50%;
    background: var(--black);
    border: 2px solid var(--red);
  }
  .cta {
    position: absolute;
    left: 58px; top: 1105px;
    width: 812px; height: 66px;
    border-radius: 33px;
    background: var(--black);
    display: flex; align-items: center; justify-content: center;
    font-size: 30px;
    white-space: nowrap;
    letter-spacing: -0.8px;
  }
  .cta-plain { color: var(--white); font-weight: 400; }
  .cta-strong { color: var(--red); font-weight: 700; }
</style>
</head>
<body>
<main class="flyer">
  <div class="fleet-photo" role="img" aria-label="Three SUVs in black, white and red parked in front of an office building with four uniformed chauffeurs standing between them"></div>

  <div class="photo-arrival" role="img" aria-label="Uniformed chauffeur helping an executive in a navy suit step out of a black SUV"></div>
  <div class="photo-chauffeurs" role="img" aria-label="Three uniformed chauffeurs in black jackets and caps standing in a row"></div>

  <div class="price-badge">
    <div class="price-amount"><sup>$</sup>499</div>
    <div class="price-term">one-way</div>
  </div>

  <header class="brand">QUORVAN RIDE</header>

  <h1>
    <span class="route route-from">DALLAS</span>
    <span class="route-divider"></span>
    <span class="route-joiner">TO</span>
    <span class="route route-to">AUSTIN</span>
  </h1>

  <ul class="features">
    <li class="feature"><span class="feature-mark"></span>Travel Dallas to Austin in a new 2025<br>Norvak Tressel for $499 one-way</li>
    <li class="feature"><span class="feature-mark"></span>We offer Comparable Prices on Door-to-Door<br>Travel Times than Bluequill Airways</li>
    <li class="feature"><span class="feature-mark"></span>Trip includes a Uniformed Chauffeur who<br>has a Commercial Drivers License (CDL)</li>
    <li class="feature"><span class="feature-mark"></span>All of our trips are insured with $500k of<br>commercial auto insurance</li>
    <li class="feature"><span class="feature-mark"></span>You can Schedule Chauffeur Pickup at Your<br>Home in Dallas</li>
    <li class="feature"><span class="feature-mark"></span>Our Passengers can Talk on Cell Phone &amp;<br>Conduct Kavlo calls Throughout Travel</li>
    <li class="feature"><span class="feature-mark"></span>Our Chauffeur will Drop You Off at Your<br>Final Destination in Austin</li>
    <li class="feature"><span class="feature-mark"></span>Our Passengers have Maximum Privacy,<br>Comfort and First-Class Amenities.</li>
    <li class="feature"><span class="feature-mark"></span>You can Schedule Chauffeur Return Pickup<br>in Austin and Return Back to Dallas.</li>
    <li class="feature"><span class="feature-mark"></span>Our Passengers Avoid Marrow Pike Airfield<br>and QHN Airport hassles &amp; delays</li>
    <li class="feature"><span class="feature-mark"></span>We offer Faster Times on Door-to-Door<br>Travel than Bluequill Airways</li>
    <li class="feature"><span class="feature-mark"></span>Member Tellbrook Chamber of Commerce,<br>Pindle Chamber of Commerce.</li>
  </ul>

  <p class="cta">
    <span class="cta-strong">Book</span>&nbsp;<span class="cta-plain">your trip</span>&nbsp;<span class="cta-strong">today</span>&nbsp;<span class="cta-plain">at</span>&nbsp;<span class="cta-strong">www.quorvanride.example</span>
  </p>
</main>
</body>
</html>
```